Label design for an exciting new Vodka brand

We need a label design for a dynamic new Vodka brand called 'Pale lantern drift Vodka'. It is a crisp and versatile liquid with a clean and smooth finish. It should appeal to 21-39 year olds, with a slight female skew. Colours, fonts and styles should be modern and relatively neutral - take inspiration from the brand pictures attached.

Target Market(s)

21-39 year olds, both male and female, but with a slight female skew

```html
<!DOCTYPE html>
<html lang="en">
<head>
<meta charset="utf-8">
<title>Pale lantern drift Vodka – Label</title>
<link rel="stylesheet" href="https://fonts.googleapis.com/css2?family=Montserrat:wght@400;500;800&display=swap">
<style>
  :root {
    --label-plum: #2b1350;
    --ink-white: #f7f8fa;
    --gold-dark: #6b3f1c;
    --gold-mid: #c9a35e;
    --gold-light: #fbecc8;
    --page: #ffffff;
  }
  html, body {
    margin: 0;
    width: 1200px;
    height: 1000px;
    overflow: hidden;
    background: var(--page);
  }
  .canvas {
    position: relative;
    width: 1200px;
    height: 1000px;
    display: flex;
    align-items: center;
    justify-content: center;
  }
  .label {
    width: 675px;
    height: 900px;
    display: block;
  }
  .label-field { fill: var(--label-plum); }
  .arc-text {
    font-family: "Montserrat", Arial, sans-serif;
    font-weight: 500;
    fill: var(--ink-white);
    letter-spacing: 7px;
  }
  .arc-text--top { font-size: 30px; }
  .arc-text--bottom { font-size: 34px; }
  .brand-name {
    font-family: "Montserrat", Arial, sans-serif;
    font-weight: 800;
    fill: var(--ink-white);
    text-anchor: middle;
  }
  .brand-type {
    font-family: "Montserrat", Arial, sans-serif;
    font-weight: 800;
    font-size: 48px;
    letter-spacing: 4px;
    fill: var(--ink-white);
    text-anchor: middle;
  }
  .volume-pill { fill: var(--ink-white); }
  .volume-text {
    font-family: "Montserrat", Arial, sans-serif;
    font-weight: 400;
    font-size: 34px;
    fill: var(--label-plum);
    text-anchor: middle;
  }
</style>
</head>
<body>
<main class="canvas">
  <svg class="label" viewBox="0 0 930 1240" xmlns="http://www.w3.org/2000/svg" aria-labelledby="label-title">
    <title id="label-title">Pale lantern drift Vodka bottle label</title>
    <defs>
      <linearGradient id="gold-band" x1="0" y1="0" x2="1" y2="0">
        <stop offset="0" stop-color="#6b3f1c"/>
        <stop offset="0.4" stop-color="#c9a35e"/>
        <stop offset="0.75" stop-color="#fbecc8"/>
        <stop offset="1" stop-color="#c9a35e"/>
      </linearGradient>
      <path id="arc-top" d="M 74 500 A 391 391 0 0 1 856 500"/>
      <path id="arc-bottom" d="M -15 700 A 480 480 0 0 0 945 700"/>
    </defs>

    <rect class="label-field" x="0" y="0" width="930" height="1240"/>
    <rect class="gold-band" x="0" y="0" width="930" height="18" fill="url(#gold-band)"/>
    <rect class="gold-band" x="0" y="1222" width="930" height="18" fill="url(#gold-band)"/>

    <text class="arc-text arc-text--top">
      <textPath href="#arc-top" startOffset="50%" text-anchor="middle">PREMIUM   QUALITY</textPath>
    </text>

    <g class="brand-lockup">
      <text class="brand-name" x="445" y="380" font-size="190" textLength="440" lengthAdjust="spacingAndGlyphs">PALE</text>
      <text class="brand-name" x="445" y="620" font-size="190" textLength="600" lengthAdjust="spacingAndGlyphs">LANTERN</text>
      <text class="brand-name" x="445" y="860" font-size="190" textLength="520" lengthAdjust="spacingAndGlyphs">DRIFT</text>
      <text class="brand-type" transform="translate(803 575) rotate(-90)">VODKA</text>
    </g>

    <rect class="volume-pill" x="288" y="998" width="344" height="59" rx="29.5"/>
    <text class="volume-text" x="460" y="1039">700ml  40%ALC</text>

    <text class="arc-text arc-text--bottom">
      <textPath href="#arc-bottom" startOffset="50%" text-anchor="middle">HAND-CRAFTED BY PROFESSIONALS</textPath>
    </text>
  </svg>
</main>
</body>
</html>
```